Strategic Planning Process

To create an infographic overviewing our strategic planning process

This is a one page infographic, portrait or landscape. Ideal size is something that fits on 8.5 by 11 paper.

I want to give designers an extra day or two to create designs. My project description was unclear.

The visual elements selection on the draft was added to offer suggestions on what to include on the infographic, not to be literally included on the infographic

```html
<!DOCTYPE html>
<html lang="en">
<head>
<meta charset="UTF-8">
<title>Achieving Strategic Alignment – Four-Step Process</title>
<link href="https://fonts.googleapis.com/css2?family=Poppins:wght@400;600;700;800&display=swap" rel="stylesheet">
<style>
  :root {
    --navy: #2b2a5e;
    --gold: #b78d4a;
    --arc: #c9c8da;
    --map: #f1f1f4;
    --muted: #55556a;
    --white: #ffffff;
  }
  * { margin: 0; padding: 0; box-sizing: border-box; }
  html, body { width: 1200px; height: 846px; overflow: hidden; background: var(--white); }
  body { font-family: "Poppins", sans-serif; color: var(--navy); }
  .canvas { position: relative; width: 1200px; height: 846px; overflow: hidden; background: var(--white); }

  .world-map {
    position: absolute; left: 98px; top: 142px; width: 1030px; height: 580px;
    background: radial-gradient(ellipse at center, var(--map) 0%, rgba(241,241,244,0.7) 55%, rgba(255,255,255,0) 78%);
    border-radius: 40px;
  }

  .process-graphic { position: absolute; left: 0; top: 0; }

  .headline { position: absolute; left: 436px; top: 278px; }
  .headline .kicker { font-size: 19px; font-weight: 400; color: var(--muted); }
  .headline .line-gold { font-size: 56px; font-weight: 800; color: var(--gold); line-height: 1; margin-top: 14px; letter-spacing: 0.3px; }
  .headline .line-navy { font-size: 64px; font-weight: 800; color: var(--navy); line-height: 1; margin-top: 8px; letter-spacing: 0.3px; }

  .step-label { position: absolute; font-size: 22px; font-weight: 600; color: var(--navy); line-height: 1.35; }
  .step-1 { left: 122px; top: 302px; }
  .step-2 { left: 405px; top: 618px; }
  .step-3 { left: 666px; top: 618px; }
  .step-4 { left: 938px; top: 318px; }

  .brand { position: absolute; right: 92px; top: 84px; display: flex; align-items: center; gap: 12px; }
  .brand .dot { width: 16px; height: 16px; border-radius: 50%; background: var(--navy); }
  .brand .name { font-size: 24px; font-weight: 700; color: var(--navy); letter-spacing: 0.3px; }

  .footer-band {
    position: absolute; left: 660px; top: 757px; width: 560px; height: 100px;
    background: var(--navy); border-top-left-radius: 70px;
    box-shadow: -6px -5px 0 0 var(--gold);
  }
  .footer-band .url { position: absolute; left: 0; width: 540px; text-align: center; top: 32px; font-size: 20px; color: var(--white); font-weight: 400; }
</style>
</head>
<body>
<div class="canvas">
  <div class="world-map" role="img" aria-label="Faint dotted world map in the background"></div>

  <svg class="process-graphic" width="1200" height="846" viewBox="0 0 1200 846">
    <path d="M320 300 C320 560 430 585 595 585 C765 585 862 515 862 230" fill="none" stroke="var(--arc)" stroke-width="33"/>
    <polygon points="822,236 902,236 862,184" fill="var(--arc)"/>

    <g class="step-node">
      <circle cx="320" cy="338" r="48" fill="var(--white)"/>
      <path d="M277 360 A48 48 0 0 1 320 290" fill="none" stroke="var(--gold)" stroke-width="3"/>
      <circle cx="320" cy="338" r="38" fill="var(--navy)"/>
      <circle cx="320" cy="338" r="14" fill="none" stroke="var(--gold)" stroke-width="3"/>
      <circle cx="320" cy="338" r="5" fill="var(--white)"/>
      <circle cx="320" cy="278" r="16" fill="var(--white)" stroke="var(--navy)" stroke-width="3"/>
      <text x="320" y="285" text-anchor="middle" font-family="Poppins, sans-serif" font-weight="700" font-size="18" fill="var(--navy)">1</text>
    </g>

    <g class="step-node">
      <circle cx="460" cy="534" r="48" fill="var(--white)"/>
      <path d="M417 556 A48 48 0 0 1 460 486" fill="none" stroke="var(--gold)" stroke-width="3"/>
      <circle cx="460" cy="534" r="38" fill="var(--navy)"/>
      <circle cx="455" cy="528" r="11" fill="none" stroke="var(--gold)" stroke-width="3"/>
      <line x1="455" y1="540" x2="455" y2="549" stroke="var(--white)" stroke-width="3"/>
      <circle cx="460" cy="487" r="16" fill="var(--white)" stroke="var(--navy)" stroke-width="3"/>
      <text x="460" y="494" text-anchor="middle" font-family="Poppins, sans-serif" font-weight="700" font-size="18" fill="var(--navy)">2</text>
    </g>

    <g class="step-node">
      <circle cx="728" cy="534" r="48" fill="var(--white)"/>
      <path d="M685 556 A48 48 0 0 1 728 486" fill="none" stroke="var(--gold)" stroke-width="3"/>
      <circle cx="728" cy="534" r="38" fill="var(--navy)"/>
      <circle cx="728" cy="530" r="13" fill="none" stroke="var(--gold)" stroke-width="3"/>
      <circle cx="728" cy="530" r="4" fill="var(--white)"/>
      <circle cx="728" cy="487" r="16" fill="var(--white)" stroke="var(--navy)" stroke-width="3"/>
      <text x="728" y="494" text-anchor="middle" font-family="Poppins, sans-serif" font-weight="700" font-size="18" fill="var(--navy)">3</text>
    </g>

    <g class="step-node">
      <circle cx="862" cy="330" r="48" fill="var(--white)"/>
      <path d="M819 352 A48 48 0 0 1 862 282" fill="none" stroke="var(--gold)" stroke-width="3"/>
      <circle cx="862" cy="330" r="38" fill="var(--navy)"/>
      <rect x="850" y="316" width="22" height="26" rx="2" fill="none" stroke="var(--gold)" stroke-width="3"/>
      <line x1="855" y1="324" x2="867" y2="324" stroke="var(--white)" stroke-width="2"/>
      <line x1="855" y1="331" x2="867" y2="331" stroke="var(--white)" stroke-width="2"/>
      <circle cx="862" cy="275" r="16" fill="var(--white)" stroke="var(--navy)" stroke-width="3"/>
      <text x="862" y="282" text-anchor="middle" font-family="Poppins, sans-serif" font-weight="700" font-size="18" fill="var(--navy)">4</text>
    </g>
  </svg>

  <div class="headline">
    <p class="kicker">Achieving Strategic Alignment</p>
    <p class="line-gold">FOUR-STEP</p>
    <p class="line-navy">PROCESS</p>
  </div>

  <p class="step-label step-1">Envision /<br>Alignment</p>
  <p class="step-label step-2">Discover<br>&amp; Reveal</p>
  <p class="step-label step-3">Reimagine</p>
  <p class="step-label step-4">Actualize</p>

  <div class="brand">
    <span class="dot"></span>
    <p class="name">Quillmere Advisory</p>
  </div>

  <div class="footer-band">
    <p class="url">www.quillmereadvisory.example</p>
  </div>
</div>
</body>
</html>
```